Ridgeline Journeys business card

please see website
www.ridgelinejourneys.comau

info needed on card
Curtis Halvey
Ph
email
Adventure Riding GPS trails

please use my logo and colours off my site

Curtis Halvey
curtis@ridgelinejourneys.com

```html
<!DOCTYPE html>
<html lang="en">
<head>
<meta charset="utf-8">
<title>Ridgeline Journeys – Business Card</title>
<link href="https://fonts.googleapis.com/css2?family=Open+Sans:wght@400;600;800&display=swap" rel="stylesheet">
<style>
  :root {
    --canvas: #e9e7e3;
    --card: #ffffff;
    --ink: #1b1b1b;
    --grey: #6a6a6a;
    --faint: #ececec;
    --gold: #f2c200;
    --gold-faint: #fbf3cf;
  }
  * { margin: 0; padding: 0; box-sizing: border-box; }
  html, body {
    width: 1200px; height: 892px; overflow: hidden;
    background: var(--canvas);
    font-family: "Open Sans", Arial, sans-serif;
    color: var(--ink);
  }
  .sheet {
    width: 1200px; height: 892px;
    display: flex; align-items: center; justify-content: center; gap: 44px;
  }
  .card {
    position: relative;
    width: 520px; height: 318px;
    background: var(--card);
    box-shadow: 0 6px 18px rgba(0,0,0,.12);
    overflow: hidden;
  }
  .brand {
    position: absolute;
    display: flex; align-items: center; gap: 22px;
  }
  .brand-mark {
    width: 70px; height: 70px; border-radius: 50%;
    background: var(--gold);
    flex: none;
  }
  .brand-name {
    font-weight: 800; font-size: 38px; line-height: 1;
    text-transform: uppercase; letter-spacing: .5px;
    color: var(--ink);
  }
  .card-front .brand { left: 62px; top: 34px; }
  .card-back .brand { left: 70px; top: 62px; }

  .rule-name {
    position: absolute; left: 0; right: 0; top: 160px;
    display: flex; align-items: center;
  }
  .rule-name::before, .rule-name::after {
    content: ""; height: 1.5px; background: var(--ink);
  }
  .rule-name::before { width: 140px; }
  .rule-name::after { flex: 1; }
  .person-name {
    font-size: 30px; font-weight: 400; padding: 0 16px; letter-spacing: .5px;
  }
  .contact {
    position: absolute; left: 44px; top: 214px;
    font-weight: 600; font-size: 17px; line-height: 1.35;
  }
  .rule-bottom {
    position: absolute; left: 290px; right: 0; top: 208px;
    height: 1.5px; background: var(--ink);
  }
  .faint-mark {
    position: absolute; border-radius: 50%; background: var(--gold-faint);
    box-shadow: 0 0 0 14px var(--faint);
  }
  .card-front .faint-mark { width: 60px; height: 60px; right: 22px; bottom: 18px; }
  .card-back .faint-mark { width: 170px; height: 170px; right: 40px; bottom: -50px; }
</style>
</head>
<body>
<main class="sheet">
  <section class="card card-front" aria-label="Card front">
    <div class="brand">
      <span class="brand-mark"></span>
      <span class="brand-name">Ridgeline<br>Journeys</span>
    </div>
    <div class="rule-name"><span class="person-name">Curtis Halvey</span></div>
    <div class="rule-bottom"></div>
    <div class="contact">
      <p>curtis@ridgelinejourneys.com</p>
      <p>www.ridgelinejourneys.com.au</p>
    </div>
    <span class="faint-mark"></span>
  </section>

  <section class="card card-back" aria-label="Card back">
    <span class="faint-mark"></span>
    <div class="brand">
      <span class="brand-mark"></span>
      <span class="brand-name">Ridgeline<br>Journeys</span>
    </div>
  </section>
</main>
</body>
</html>
```